Website for Barlow Fabrication & Building Ltd

General Note to all.

1. Piling and gas works are separate areas of work and should not be put together.
- the marine section should really be the piling works and should have all the barges/water piles etc.
- the gas section should have the big silo looking thing

2. I would like to add in Specialist Onsite Labour and Management in the 'our services' section. The would include the Supervisors, Coded Welders, Site Fitters and Crane and Rig Crews etc.

3. I did like it how someone had use the BFB header logo as the top of the webpage with the individual tabs above and the website starting below. Please remove the VAT number and phone number from this section.

4. I also liked how one designer incorporate the orange line with spark (from the logo) as a page separator representing the welding part of the business

5. Add in a Mission Statement - To go above and beyond in to ensure our clients projects are delivered safely, ahead of schedule, in any environment for the benefit of not only our customers but also our employees and communities we work in.

6. Add in Business Objectives -BFB is on a mission to be one of the leading contractors in UK to supply All Site Labour - ranging from Site Management, fully Coded Welders, Site Fitters and Crane and Rig Crews.

7. I am happy for you to add in photos that are not ours for the thumbs nails for the our services. ie a colourful welding pics/cool tunnelling pic etc - just make sure I will not get done for copy write infringements

8. I would like a some type of 'contact us' field or 'request a consultation' section.

9. Please confirm if the webpages you create will be compatible for both desktop and mobile app and how difficult it will be to update personally once it is live.

10. You have all done very well and have thus far been very impressed with what you have produced. I gave a very vague brief as I was not entirely sure how you would go about making something with very little information. Some of the designs look very professional.

11. I'm not sure how once I choose the winning design how that then transfers over to my domain? Perhaps someone can help me with that? I will also be looking for a web hosting platform so feel free to provide this information.

After using Sketch hive for successful getting a professional logo for the company I'm giving the web design option a go.

I am looking for a professional website for the above civil construction company.

The company director has many years experience in Marine, tunnelling, conveyors, stadium construction gas and piling works including piling works for coal ports, bridges and tunnels.

The company currently provide 20+ skilled and experienced guys from all trades (supervisors, coded welders, fitters, crane drivers and crane supervisors, rigglers, slingers and piling operatives) on the Corran Shoreline project in London - London's new super sewer. Most of this work is off barges carrying cranes (upto 600T and drill rigs).

As we are looking to expand and get more subcontracts we need a web presence to say who we are and what we do.

I'll include the 2 company logos we currently use below

I have included an info doc with pics you may or may not use.

Target Market(s)

Mainly other large construction companies and potential subcontractors

Industry/Entity Type

Construction Company

Coding

Coded - Design and coding required

Font styles to use
Sans Serif

Colors
0655a3
f37122
ffffff

Requirements
Must have
• Few tabs
• Simple to use/update but still professional look
• The challenge will be making the website look professional with not much available content.
Should not have
• No residential house building

```html
<!DOCTYPE html>
<html lang="en">
<head>
<meta charset="utf-8">
<title>Barlow Fabrication & Building Ltd</title>
<link href="https://fonts.googleapis.com/css2?family=Exo+2:wght@500;600;700&family=Open+Sans:ital,wght@0,400;0,600;1,400&display=swap" rel="stylesheet">
<style>
:root{
  --blue:#0655a3;
  --navy:#0c3a8e;
  --orange:#f37122;
  --orange-deep:#ee5a1f;
  --white:#ffffff;
  --ink:#333333;
  --muted:#666666;
  --light:#f3f4f6;
  --grey:#e9ebee;
  --partner:#f1f1f1;
}
*{box-sizing:border-box;margin:0;padding:0}
html,body{width:1200px;height:3120px;overflow:hidden}
body{font-family:"Open Sans",Arial,sans-serif;color:var(--ink);background:var(--white);position:relative}
.heading{font-family:"Exo 2",Arial,sans-serif}
a{color:inherit;text-decoration:none}

/* top bar */
.topbar{position:absolute;left:0;top:0;width:1200px;height:52px}
.topbar-shape{position:absolute;left:0;top:0}
.social{position:absolute;left:120px;top:10px;display:flex;gap:8px}
.social span{width:30px;height:30px;border:1.5px solid var(--white);border-radius:50%;display:block}
.top-contact{position:absolute;right:148px;top:15px;display:flex;gap:40px;color:var(--white);font-size:13px;font-weight:600}
.top-contact div{display:flex;align-items:center;gap:10px}

/* header */
.header{position:absolute;top:52px;left:0;width:1200px;height:120px;background:var(--white)}
.brand{position:absolute;left:86px;top:26px;display:flex;align-items:center;gap:10px}
.brand-dot{width:56px;height:56px;border:3px solid var(--blue);border-radius:50%}
.brand-name{font-family:"Exo 2",Arial,sans-serif;font-weight:700;font-size:38px;color:var(--blue)}
.nav{position:absolute;right:140px;top:52px;display:flex;gap:40px;font-size:12.5px;font-weight:600;color:var(--ink)}
.nav .active{color:var(--orange)}
.search{position:absolute;right:85px;top:44px;width:48px;height:48px;border:2px solid var(--orange);border-radius:50%;display:flex;align-items:center;justify-content:center}

/* hero */
.hero{position:absolute;top:172px;left:0;width:1200px;height:556px;background:linear-gradient(100deg,#7c8a5c 0%,#8e9488 30%,#6f7470 55%,#3f4447 100%)}
.hero-text{position:absolute;left:712px;top:310px;width:420px;color:var(--white)}
.hero-title{font-family:"Exo 2",Arial,sans-serif;font-size:38px;font-weight:700;color:var(--orange);letter-spacing:1px;line-height:1}
.hero-sub{font-family:"Exo 2",Arial,sans-serif;font-size:28px;font-weight:600;letter-spacing:1px;margin-top:12px}
.hero-copy{font-size:11.5px;line-height:24px;margin-top:16px}

/* about */
.about{position:absolute;top:728px;left:0;width:1200px;height:557px;background:var(--light)}
.about-frame{position:absolute;left:170px;top:80px;width:355px;height:418px;border:2px solid var(--orange)}
.about-photo{position:absolute;left:185px;top:67px;width:357px;height:415px;background:linear-gradient(135deg,#b9bcae 0%,#a7c53f 45%,#e8793b 80%,#8a8f8a 100%)}
.about-text{position:absolute;left:595px;top:78px;width:470px}
.about-title{font-size:36px;font-weight:600;color:#444;line-height:1}
.about-sub{font-size:21px;font-weight:600;color:var(--orange);margin-top:12px}
.about-copy{font-size:11.5px;line-height:27px;color:var(--muted);margin-top:16px}
.btn{display:inline-block;background:var(--orange-deep);color:var(--white);font-size:12.5px;font-weight:600;padding:12px 26px;margin-top:20px;border-radius:2px}

/* services */
.services{position:absolute;top:1285px;left:0;width:1200px;height:400px;background:var(--grey);text-align:center}
.section-title{font-size:27px;font-weight:700;color:var(--blue);letter-spacing:.5px}
.section-sub{font-size:11.5px;color:var(--muted);margin-top:12px}
.services .section-title{margin-top:38px}
.service-list{position:absolute;top:155px;left:104px;width:996px;display:flex;justify-content:space-between}
.service{width:300px;display:flex;flex-direction:column;align-items:center}
.service svg{height:66px}
.service h3{font-family:"Exo 2",Arial,sans-serif;font-size:17px;font-weight:700;color:var(--blue);margin-top:8px}
.service p{font-size:11.5px;line-height:24px;color:var(--ink);margin-top:10px;width:250px}
.service.feature h3{color:var(--orange)}

/* mission */
.mission{position:absolute;top:1685px;left:0;width:1200px;height:285px;background:var(--orange-deep);text-align:center;color:var(--white)}
.stars{margin-top:56px;display:flex;justify-content:center}
.quote{font-style:italic;font-size:17px;line-height:32px;color:#fde3d3;margin:14px auto 0;width:760px}
.author{font-size:16px;margin-top:16px;font-weight:600;letter-spacing:.5px}
.arrow{position:absolute;top:122px}

/* projects */
.projects{position:absolute;top:1970px;left:0;width:1200px;height:555px;background:var(--white);text-align:center}
.projects .section-title{margin-top:40px}
.project-list{position:absolute;top:132px;left:85px;width:1030px;display:flex;justify-content:space-between}
.project{width:325px}
.project-photo{height:213px;position:relative}
.tag{position:absolute;left:50%;transform:translateX(-50%);bottom:-18px;background:var(--orange-deep);color:var(--white);font-size:12px;padding:8px 22px;white-space:nowrap}
.project h4{font-size:15.5px;font-weight:600;color:#444;margin-top:48px;letter-spacing:.3px}
.project p{font-size:11.5px;line-height:25px;color:var(--muted);margin-top:12px}

/* partners */
.partners{position:absolute;top:2525px;left:0;width:1200px;height:188px;background:var(--partner)}
.partner{position:absolute;top:45px;width:172px;height:97px;background:var(--white);display:flex;align-items:center;justify-content:center}
.partner span{display:block}
.chev{position:absolute;top:72px}

/* footer */
.footer{position:absolute;top:2713px;left:0;width:1200px;height:407px;background:var(--navy);color:var(--white)}
.footer-brand{position:absolute;left:50%;top:24px;transform:translateX(-50%);display:flex;align-items:center;gap:12px}
.footer-brand .brand-dot{width:64px;height:64px;border-color:var(--white)}
.footer-brand .brand-name{color:var(--white);font-size:42px}
.col{position:absolute;top:170px;font-size:11.5px}
.col h5{font-family:"Exo 2",Arial,sans-serif;font-size:16px;font-weight:600;letter-spacing:.5px;margin-bottom:18px}
.contact-col{left:157px;width:240px;line-height:20px}
.contact-row{display:flex;align-items:center;gap:12px;margin-top:14px}
.links-col{left:480px}
.links{display:grid;grid-template-columns:120px 120px;row-gap:14px}
.consult-col{left:772px;width:340px}
.signup{display:flex;margin-top:22px}
.signup .field{width:290px;height:44px;background:var(--white);color:var(--ink);font-size:11.5px;padding:14px}
.signup .send{width:44px;height:44px;background:var(--orange-deep);display:flex;align-items:center;justify-content:center}
.copyright{position:absolute;top:368px;width:100%;text-align:center;font-size:11.5px}
</style>
</head>
<body>

<header class="topbar">
  <svg class="topbar-shape" width="1200" height="52" viewBox="0 0 1200 52"><polygon points="85,0 1115,0 1090,52 110,52" fill="#0c3a8e"/></svg>
  <div class="social"><span></span><span></span><span></span><span></span><span></span></div>
  <div class="top-contact">
    <div><svg width="15" height="11" viewBox="0 0 15 11"><rect x="0.5" y="0.5" width="14" height="10" fill="#fff"/><polyline points="1,1 7.5,6 14,1" fill="none" stroke="#0c3a8e" stroke-width="1.2"/></svg>EMAIL : info@bfb-build.co.uk</div>
    <div><svg width="13" height="13" viewBox="0 0 24 24"><path d="M6.6 10.8a15 15 0 0 0 6.6 6.6l2.2-2.2c.3-.3.7-.4 1-.2 1.1.4 2.3.6 3.6.6.6 0 1 .4 1 1V20c0 .6-.4 1-1 1A17 17 0 0 1 3 4c0-.6.4-1 1-1h3.5c.6 0 1 .4 1 1 0 1.3.2 2.5.6 3.6.1.3 0 .7-.2 1z" fill="#fff"/></svg>CALL US : (000)-555-0142</div>
  </div>
</header>

<div class="header">
  <div class="brand"><span class="brand-dot"></span><span class="brand-name">BFB</span></div>
  <nav class="nav"><a class="active">HOME</a><a>ABOUT US</a><a>SERVICES</a><a>PROJECTS</a><a>NEWS</a><a>CONTACT US</a></nav>
  <div class="search"><svg width="14" height="14" viewBox="0 0 14 14"><circle cx="6" cy="6" r="4.5" fill="none" stroke="#f37122" stroke-width="2"/><line x1="9.3" y1="9.3" x2="13" y2="13" stroke="#f37122" stroke-width="2"/></svg></div>
</div>

<section class="hero" role="img" aria-label="Surveyor with a tripod level on a road construction site with a roller behind">
  <div class="hero-text">
    <div class="hero-title">BARLOW</div>
    <div class="hero-sub">FABRICATION &amp; BUILDING</div>
    <p class="hero-copy">BFB is on a mission to be one of the leading contractors in UK to supply All Site Labour - ranging from Site Management, fully Coded Welders, Site Fitters and Crane and Rig Crews.</p>
  </div>
</section>

<section class="about">
  <div class="about-frame"></div>
  <div class="about-photo" role="img" aria-label="Two engineers in hard hats and hi-vis jackets reviewing a laptop on site"></div>
  <div class="about-text">
    <h2 class="about-title heading">ABOUT OUR</h2>
    <h3 class="about-sub heading">BARLOW FABRICATION &amp; BUILDING</h3>
    <p class="about-copy">Daniel Barlow was born and raised in South East London After finishing school he completed a Welding and Fabrication apprenticeship with Kerr &amp; Hale Welders and Ridgeway Civils. During this time he gained a lot of experience in structural steel welding becoming a coded welder and working on both the Dome Arena and Riverside stadiums.</p>
    <p class="about-copy">Soon after completing his apprenticeship he moved over to Australia and was fortunate to work for some of the most prestigious civil construction companies: Hollis Marsh, CK&amp;T Group and Stonebridge. Here he was also able to gain additional qualifications in Rigging Crane Operating making him an exceptional all-rounder on sites.</p>
    <a class="btn">READ MORE</a>
  </div>
</section>

<section class="services">
  <h2 class="section-title heading">OUR SERVICES</h2>
  <p class="section-sub">Piling, gas works and specialist onsite labour for marine, tunnelling, conveyor and stadium projects across the UK</p>
  <div class="service-list">
    <div class="service">
      <svg viewBox="0 0 60 66" width="60"><g fill="none" stroke="#0655a3" stroke-width="5" stroke-linecap="round"><circle cx="30" cy="9" r="5"/><line x1="30" y1="14" x2="30" y2="60"/><line x1="18" y1="24" x2="42" y2="24"/><path d="M6 40 Q10 60 30 60 Q50 60 54 40"/></g></svg>
      <h3>PILING WORKS</h3>
      <p>Barge mounted piling, drill rigs and water piles for ports, bridges, tunnels and the Corran Shoreline project</p>
    </div>
    <div class="service feature">
      <svg viewBox="0 0 66 66" width="66"><path d="M14 62 V20 A19 12 0 0 1 52 20 V62 Z" fill="#f37122"/><g stroke="#fff" stroke-width="3"><line x1="14" y1="32" x2="52" y2="32"/><line x1="14" y1="46" x2="52" y2="46"/></g><line x1="6" y1="62" x2="60" y2="62" stroke="#f37122" stroke-width="4"/></svg>
      <h3>GAS WORKS</h3>
      <p>Fabrication and installation of gas holders, silos and pipework delivered safely by fully coded welders</p>
    </div>
    <div class="service">
      <svg viewBox="0 0 66 66" width="66"><g fill="none" stroke="#0655a3" stroke-width="4" stroke-linejoin="round"><path d="M12 46 A21 21 0 0 1 54 46"/><line x1="33" y1="25" x2="33" y2="36"/><rect x="6" y="46" width="54" height="8" rx="3"/></g></svg>
      <h3>SPECIALIST ONSITE LABOUR</h3>
      <p>Supervisors, coded welders, site fitters and crane and rig crews, with full site management</p>
    </div>
  </div>
</section>

<section class="mission">
  <svg class="arrow" style="left:175px" width="24" height="40" viewBox="0 0 24 40"><polyline points="20,4 5,20 20,36" fill="none" stroke="#fff" stroke-width="4"/></svg>
  <svg class="arrow" style="right:175px" width="24" height="40" viewBox="0 0 24 40"><polyline points="4,4 19,20 4,36" fill="none" stroke="#fff" stroke-width="4"/></svg>
  <div class="stars">
    <svg width="120" height="28" viewBox="0 0 120 28"><g fill="#ffd21f"><polygon id="s" points="14,1 17.6,10 27,10.4 19.6,16.4 22.2,26 14,20.6 5.8,26 8.4,16.4 1,10.4 10.4,10"/><use href="#s" x="30"/><use href="#s" x="60"/><use href="#s" x="90"/></g></svg>
  </div>
  <p class="quote">&#8220;To go above and beyond to ensure our clients projects are delivered safely, ahead of schedule, in any environment for the benefit of not only our customers but also our employees and communities we work in.&#8221;</p>
  <p class="author">OUR MISSION STATEMENT</p>
</section>

<section class="projects">
  <h2 class="section-title heading">OUR PROJECTS</h2>
  <p class="section-sub">Sed ut perspiciatis unde omnis iste natus error sit voluptatem accusantium doloremque laudantium, totam rem aperiam</p>
  <div class="project-list">
    <article class="project">
      <div class="project-photo" role="img" aria-label="Crane barge on a river under blue sky" style="background:linear-gradient(180deg,#3f7fd0 0%,#8ab6e4 55%,#6f6a58 75%,#3a4a5a 100%)"><span class="tag">06 JUN 2018 &nbsp;|&nbsp; COMMENT</span></div>
      <h4>SED UT PERSPICIATIS UNDE</h4>
      <p>Sed ut perspiciatis unde omnis iste natus error sit voluptatem accusantium doloremque laudantium, beatae vitae dicta sunt explicabo.</p>
    </article>
    <article class="project">
      <div class="project-photo" role="img" aria-label="Piling rigs on a barge over dark water" style="background:linear-gradient(180deg,#2f63b8 0%,#6d9bd8 50%,#3a3a38 72%,#1f2a38 100%)"><span class="tag">06 JUN 2018 &nbsp;|&nbsp; COMMENT</span></div>
      <h4>SED UT PERSPICIATIS UNDE</h4>
      <p>Sed ut perspiciatis unde omnis iste natus error sit voluptatem accusantium doloremque laudantium, beatae vitae dicta sunt explicabo.</p>
    </article>
    <article class="project">
      <div class="project-photo" role="img" aria-label="Floating work platform on a river at sunset" style="background:linear-gradient(180deg,#2e5fb0 0%,#7aa2d6 45%,#d8935a 62%,#2a2f3a 80%,#1a2230 100%)"><span class="tag">06 JUN 2018 &nbsp;|&nbsp; COMMENT</span></div>
      <h4>SED UT PERSPICIATIS UNDE</h4>
      <p>Sed ut perspiciatis unde omnis iste natus error sit voluptatem accusantium doloremque laudantium, beatae vitae dicta sunt explicabo.</p>
    </article>
  </div>
</section>

<section class="partners" aria-label="Partners">
  <svg class="chev" style="left:48px" width="20" height="46" viewBox="0 0 20 46"><polyline points="18,2 3,23 18,44" fill="none" stroke="#cfcfcf" stroke-width="2"/></svg>
  <svg class="chev" style="right:48px" width="20" height="46" viewBox="0 0 20 46"><polyline points="2,2 17,23 2,44" fill="none" stroke="#cfcfcf" stroke-width="2"/></svg>
  <div class="partner" style="left:108px"><span style="width:120px;height:18px;background:#1f3a8a"></span></div>
  <div class="partner" style="left:313px"><span style="width:44px;height:60px;background:#2e3440"></span></div>
  <div class="partner" style="left:518px"><span style="width:70px;height:64px;background:#e7c21a"></span></div>
  <div class="partner" style="left:724px"><span style="width:100px;height:60px;border-radius:50%;background:#2c6fb7"></span></div>
  <div class="partner" style="left:928px"><span style="width:110px;height:50px;background:#3aa14a"></span></div>
</section>

<footer class="footer">
  <div class="footer-brand"><span class="brand-dot"></span><span class="brand-name">BFB</span></div>
  <div class="col contact-col">
    <h5>CONTACT US</h5>
    <p>#12 Wharf Road Dock Lane<br>Lorem Ipsum</p>
    <div class="contact-row"><svg width="14" height="14" viewBox="0 0 24 24"><path d="M6.6 10.8a15 15 0 0 0 6.6 6.6l2.2-2.2c.3-.3.7-.4 1-.2 1.1.4 2.3.6 3.6.6.6 0 1 .4 1 1V20c0 .6-.4 1-1 1A17 17 0 0 1 3 4c0-.6.4-1 1-1h3.5c.6 0 1 .4 1 1 0 1.3.2 2.5.6 3.6.1.3 0 .7-.2 1z" fill="#fff"/></svg>Phone : (000)-555-0142</div>
    <div class="contact-row"><svg width="15" height="11" viewBox="0 0 15 11"><rect x="0.7" y="0.7" width="13.6" height="9.6" fill="none" stroke="#fff" stroke-width="1.3"/><polyline points="1,1 7.5,6 14,1" fill="none" stroke="#fff" stroke-width="1.3"/></svg>Email : info@bfb-build.co.uk</div>
  </div>
  <div class="col links-col">
    <h5>QUICK LINKS</h5>
    <div class="links"><a>Home</a><a>Projects</a><a>About Us</a><a>News</a><a>Services</a><a>Contact Us</a></div>
  </div>
  <div class="col consult-col">
    <h5>REQUEST A CONSULTATION</h5>
    <p>Leave your email and our team will call you back</p>
    <div class="signup"><div class="field">Enter Your Email Id :</div><div class="send"><svg width="18" height="18" viewBox="0 0 24 24"><path d="M2 11 22 2 15 22 11 13z" fill="#fff"/></svg></div></div>
  </div>
  <p class="copyright">© Copyright 2018 Barlow Fabrication &amp; Building All Rights Reserved</p>
</footer>

</body>
</html>
```